Creation of brand identity and website "Tandem K"

I am currently seeking an brand, identity and web design for a new project called Tandem K. This is a brand new concept from scratch and you have free-reign on the whole design process, taking into account my preference below.

Must include the name "Tandem K", or "Tandem K: Or the year I woke Up". Kudos is this forms part of the brands logo

Design that can be easily scaled to potentially include: a blog, timeline and vlogs.

Minimal but effective use of colour (however any colours and combinations permitted

Use of icons/graphics over text wherever possible

Minimal use of frames and borders

I appreciate this is a fairly wide scope so please contact me on marblefinch@postwillow.com with any questions or more information on what the project is.

Target Market(s)

Male and Female 20-40
Blog readers
Selfhelp

Industry/Entity Type

Seeking

Number of Pages Required

1 page

Font styles to use
Serif
Sans Serif

Requirements
Must have
• It is in effect a blog design, so about me section, recent blog / archived posts, reader comments / Q and A section.
• A coded design would be appreciated to make my life easier however I have left the design as uncoded as getting the right design matters more to me and I want to keep the project open to as many designers as possible
Nice to have
• See project description for other details and please ask if you need anything else :)
Should not have
• Mustn't be cluttered or feel fussy
• Promote icons over text
• Frames / multiple borders

```html
<!DOCTYPE html>
<html lang="en">
<head>
<meta charset="utf-8">
<title>Tandem K</title>
<link href="https://fonts.googleapis.com/css2?family=Montserrat:wght@500;600;700&family=Lato:ital,wght@0,400;0,700;1,400&display=swap" rel="stylesheet">
<style>
  :root{
    --green:#8cc63f;
    --green-dark:#76ad2c;
    --ink:#1e1e1e;
    --text:#3d3d3d;
    --muted:#7a7a7a;
    --line:#dedede;
    --card:#fafafa;
    --footer:#141414;
  }
  *{box-sizing:border-box;margin:0;padding:0}
  html,body{width:750px;height:1200px;overflow:hidden;background:#fff}
  body{font-family:"Lato",sans-serif;color:var(--text)}
  .page{position:relative;width:938px;height:1500px;transform:scale(.8);transform-origin:0 0}
  .abs{position:absolute}

  /* header */
  .site-header{left:0;top:0;width:938px;height:50px;border-bottom:1px solid var(--line);background:#fff}
  .brand{left:76px;top:11px;font-family:"Montserrat",sans-serif;font-weight:700;font-size:23px;color:var(--ink)}
  .nav{left:389px;top:23px;display:flex;align-items:center;font-family:"Montserrat",sans-serif;font-weight:600;font-size:10.5px;color:var(--ink)}
  .nav span{padding:0 10px;border-left:1px solid #999;line-height:8px}
  .nav span:first-child{padding-left:0;border-left:0}
  .nav .active{color:var(--green)}
  .social{left:769px;top:14px;display:flex;gap:6px}
  .social i{display:block;width:26px;height:26px;border-radius:50%;background:var(--ink)}
  .social i:first-child{background:var(--green)}

  /* hero */
  .hero-photo{left:0;top:50px;width:598px;height:362px;background:linear-gradient(160deg,#e9eedc 0%,#c7d79a 35%,#8fb54a 70%,#5e8f26 100%)}
  .hero-caption{left:0;top:377px;width:598px;height:35px;background:rgba(140,198,63,.85);padding-left:76px;font-family:"Montserrat",sans-serif;font-weight:700;font-size:19px;line-height:35px;color:var(--ink)}
  .about{left:598px;top:50px;width:340px;height:362px;background:linear-gradient(180deg,#4c4f45 0%,#3f4a30 55%,#3a5a1e 100%);text-align:center;color:#fff}
  .avatar{position:absolute;left:67px;top:27px;width:130px;height:130px;border-radius:50%;border:4px solid #fff;background:linear-gradient(180deg,#cfe0ee,#9bb4c6)}
  .about h2{position:absolute;left:0;width:265px;top:170px;font-family:"Montserrat",sans-serif;font-weight:500;font-size:17px}
  .about p{position:absolute;left:14px;width:240px;top:200px;font-size:10.5px;line-height:16px;color:#eee}
  .btn{display:inline-block;background:var(--green);color:#fff;font-family:"Montserrat",sans-serif;font-weight:700;font-size:10.5px;border-radius:2px}
  .about .btn{position:absolute;left:90px;top:301px;width:83px;height:23px;line-height:23px}

  /* posts */
  .section-title{left:76px;top:433px;font-family:"Montserrat",sans-serif;font-weight:700;font-size:22px;color:var(--ink)}
  .section-title em,.box-title em{font-style:normal;color:var(--green)}
  .post{left:76px;width:503px;height:161px;background:var(--card);border:1px solid #eee;box-shadow:0 1px 2px rgba(0,0,0,.06)}
  .post .thumb{position:absolute;left:0;top:0;width:161px;height:161px}
  .post h3{position:absolute;left:182px;top:20px;font-family:"Montserrat",sans-serif;font-weight:600;font-size:14.5px;color:var(--ink)}
  .meta{position:absolute;left:182px;top:48px;display:flex;gap:12px;font-size:9px;color:var(--text);align-items:center}
  .meta span{display:flex;align-items:center;gap:5px}
  .post p{position:absolute;left:182px;top:74px;width:305px;font-size:9.5px;line-height:15.2px;color:#333}
  .more{position:absolute;right:0;bottom:0;width:27px;height:27px;background:var(--green)}

  /* sidebar */
  .box{left:627px;width:235px;border:2px solid #e6e6e6;background:#fff}
  .box-title{height:34px;border-bottom:2px solid #e6e6e6;padding-left:12px;display:flex;align-items:center;gap:7px;font-family:"Montserrat",sans-serif;font-weight:700;font-size:13.5px;color:var(--ink)}
  .search-input{margin:11px 10px;height:28px;border:1px solid var(--line);display:flex;align-items:center;justify-content:space-between;padding:0 8px;font-size:9px;font-style:italic;color:#999}
  .tabs{display:flex;height:33px;border-bottom:2px solid #e6e6e6}
  .tabs span{flex:1;display:flex;align-items:center;justify-content:center;gap:4px;border-left:2px solid #e6e6e6;font-family:"Montserrat",sans-serif;font-weight:600;font-size:10px;color:var(--ink)}
  .tabs span:first-child{border-left:0}
  .tabs i{width:12px;height:12px;border-radius:50%;background:var(--ink)}
  .tabs span:first-child i{background:var(--green)}
  .feed{padding:0 10px}
  .feed li{list-style:none;display:flex;gap:7px;padding:13px 0 12px;border-bottom:1px dashed #e2e2e2;height:66px}
  .feed li:last-child{border-bottom:0}
  .feed .face{flex:none;width:40px;height:40px;background:linear-gradient(160deg,#8a6a55,#3b2b22)}
  .feed p{font-size:8px;line-height:13px;color:#333}
  .like{display:inline-flex;align-items:center;gap:2px;border:1px solid #c8d0e0;padding:0 3px;font-size:7px;color:#4a5e8c;margin-top:2px}
  .archive{padding:0 10px}
  .archive li{list-style:none;height:28px;line-height:28px;border-bottom:1px dashed #e2e2e2;font-size:10.5px;color:#333;padding-left:16px;position:relative}
  .archive li:last-child{border-bottom:0}
  .archive li::before{content:"";position:absolute;left:3px;top:13px;width:3px;height:3px;border-radius:50%;background:var(--green)}
  .view-all{margin-left:auto;margin-right:11px;font-size:9px;color:var(--ink);font-weight:600}
  .faq{padding:10px 10px 0 10px}
  .faq li{list-style:none;position:relative;padding-left:20px;font-size:10.5px;line-height:18px;color:#222;margin-bottom:9px}
  .faq li.open{font-family:"Montserrat",sans-serif;font-weight:600;font-size:10px}
  .faq li svg{position:absolute;left:0;top:5px}
  .faq li .dot{position:absolute;left:2px;top:8px;width:3px;height:3px;border-radius:50%;background:var(--green)}
  .news{padding:14px 12px}
  .news p{font-size:10.5px;color:#222;margin-bottom:10px}
  .news .field{height:27px;width:198px;border:1px solid var(--line);font-size:9px;font-style:italic;color:#999;padding-left:8px;line-height:25px;margin-bottom:8px}
  .news .btn{width:70px;height:25px;line-height:25px;text-align:center;font-size:9.5px}

  .site-footer{left:0;top:1467px;width:938px;height:33px;background:var(--footer);color:#fff;text-align:center;font-family:"Montserrat",sans-serif;font-weight:600;font-size:8.5px;line-height:33px}
</style>
</head>
<body>
<div class="page">

  <header class="site-header abs">
    <div class="brand abs">Tandem K</div>
    <nav class="nav abs">
      <span class="active">About Me</span><span>Recent Blog</span><span>Reader Comments</span><span>Contact Us</span>
    </nav>
    <div class="social abs" aria-label="Social profiles"><i></i><i></i><i></i></div>
  </header>

  <div class="hero-photo abs" role="img" aria-label="Smiling woman in a white dress running through a sunny meadow holding yellow flowers"></div>
  <div class="hero-caption abs">Lorem ipsum dolor sit amet, consecit adipiscing elit</div>

  <section class="about abs">
    <div class="avatar" role="img" aria-label="Portrait photo of the author"></div>
    <h2>ABOUT ME</h2>
    <p>Lorem ipsum dolor sit amet, consecit adipiscing elit, sed do eiusmod tempor iLorem ipsum dolor sit amet, consecit adipiscing elit, sed do eiusmod tempor incidimen labore n dolormelaboris ni ut aliquip ex ena lin consequat</p>
    <span class="btn">READ MORE</span>
  </section>

  <h2 class="section-title abs"><em>Recent</em> Blogs</h2>

  <!-- posts -->
  <article class="post abs" style="top:485px">
    <div class="thumb" role="img" aria-label="Woman with outstretched arms under a bright blue sky" style="background:linear-gradient(180deg,#4f8fc7,#a9cde6 60%,#c58bb0)"></div>
    <h3>Lorem ipsum dolor sit</h3>
    <div class="meta"><span><svg width="9" height="9"><rect x=".5" y="1.5" width="8" height="7" fill="none" stroke="#8cc63f"/><line x1=".5" y1="3.5" x2="8.5" y2="3.5" stroke="#8cc63f"/></svg>02/07/2016</span><span><svg width="11" height="9"><ellipse cx="5.5" cy="4" rx="5" ry="3.6" fill="#8cc63f"/></svg>21 commets</span><span><svg width="11" height="10"><path d="M1 4h2v6H1zM4 4l3-4c1 0 1.5.5 1 2.5h2.5c.6 0 1 .6.8 1.2L10 9.5H4z" fill="#8cc63f"/></svg>Like Us</span><span><svg width="10" height="10"><circle cx="8" cy="2" r="1.6" fill="#8cc63f"/><circle cx="2" cy="5" r="1.6" fill="#8cc63f"/><circle cx="8" cy="8" r="1.6" fill="#8cc63f"/><path d="M8 2L2 5l6 3" stroke="#8cc63f" fill="none"/></svg>Share</span></div>
    <p>Lorem ipsum dolor sit amet, consecit adipiscing elit, sed do eiusmod tempor incidimen labore n dolorme laboris ni ut aliquip ex ena lin consequat Duis aute lorem is irure dolor in reprehenderit magna aliqua. Ut enim ad is qnexercitation ullamco.</p>
    <span class="more"><svg width="27" height="27"><path d="M10 9l4 4.5-4 4.5M14 9l4 4.5-4 4.5" stroke="#fff" stroke-width="1.3" fill="none"/></svg></span>
  </article>

  <article class="post abs" style="top:682px">
    <div class="thumb" role="img" aria-label="Young woman with pink hair standing on a sandy beach" style="background:linear-gradient(180deg,#b9d4e4,#d8e4e6 45%,#c9a489 75%,#a8826a)"></div>
    <h3>Lorem ipsum dolor sit</h3>
    <div class="meta"><span><svg width="9" height="9"><rect x=".5" y="1.5" width="8" height="7" fill="none" stroke="#8cc63f"/><line x1=".5" y1="3.5" x2="8.5" y2="3.5" stroke="#8cc63f"/></svg>02/07/2015</span><span><svg width="11" height="9"><ellipse cx="5.5" cy="4" rx="5" ry="3.6" fill="#8cc63f"/></svg>21 commets</span><span><svg width="11" height="10"><path d="M1 4h2v6H1zM4 4l3-4c1 0 1.5.5 1 2.5h2.5c.6 0 1 .6.8 1.2L10 9.5H4z" fill="#8cc63f"/></svg>Like Us</span><span><svg width="10" height="10"><circle cx="8" cy="2" r="1.6" fill="#8cc63f"/><circle cx="2" cy="5" r="1.6" fill="#8cc63f"/><circle cx="8" cy="8" r="1.6" fill="#8cc63f"/><path d="M8 2L2 5l6 3" stroke="#8cc63f" fill="none"/></svg>Share</span></div>
    <p>Lorem ipsum dolor sit amet, consecit adipiscing elit, sed do eiusmod tempor incidimen labore n dolorme laboris ni ut aliquip ex ena lin consequat Duis aute lorem is irure dolor in reprehenderit magna aliqua. Ut enim ad is qnexercitation ullamco.</p>
    <span class="more"><svg width="27" height="27"><path d="M10 9l4 4.5-4 4.5M14 9l4 4.5-4 4.5" stroke="#fff" stroke-width="1.3" fill="none"/></svg></span>
  </article>

  <article class="post abs" style="top:879px">
    <div class="thumb" role="img" aria-label="Black and white photo of a smiling couple" style="background:linear-gradient(135deg,#1a1a1a,#5a5a5a 55%,#cfcfcf)"></div>
    <h3>Lorem ipsum dolor sit</h3>
    <div class="meta"><span><svg width="9" height="9"><rect x=".5" y="1.5" width="8" height="7" fill="none" stroke="#8cc63f"/><line x1=".5" y1="3.5" x2="8.5" y2="3.5" stroke="#8cc63f"/></svg>02/07/2016</span><span><svg width="11" height="9"><ellipse cx="5.5" cy="4" rx="5" ry="3.6" fill="#8cc63f"/></svg>21 commets</span><span><svg width="11" height="10"><path d="M1 4h2v6H1zM4 4l3-4c1 0 1.5.5 1 2.5h2.5c.6 0 1 .6.8 1.2L10 9.5H4z" fill="#8cc63f"/></svg>Like Us</span><span><svg width="10" height="10"><circle cx="8" cy="2" r="1.6" fill="#8cc63f"/><circle cx="2" cy="5" r="1.6" fill="#8cc63f"/><circle cx="8" cy="8" r="1.6" fill="#8cc63f"/><path d="M8 2L2 5l6 3" stroke="#8cc63f" fill="none"/></svg>Share</span></div>
    <p>Lorem ipsum dolor sit amet, consecit adipiscing elit, sed do eiusmod tempor incidimen labore n dolorme laboris ni ut aliquip ex ena lin consequat Duis aute lorem is irure dolor in reprehenderit magna aliqua. Ut enim ad is qnexercitation ullamco.</p>
    <span class="more"><svg width="27" height="27"><path d="M10 9l4 4.5-4 4.5M14 9l4 4.5-4 4.5" stroke="#fff" stroke-width="1.3" fill="none"/></svg></span>
  </article>

  <article class="post abs" style="top:1076px">
    <div class="thumb" role="img" aria-label="Family jumping in a field of red poppies under a blue sky" style="background:linear-gradient(180deg,#dbe8f2,#a8c6de 50%,#7f9a4f 80%,#c24a2c)"></div>
    <h3>Lorem ipsum dolor sit</h3>
    <div class="meta"><span><svg width="9" height="9"><rect x=".5" y="1.5" width="8" height="7" fill="none" stroke="#8cc63f"/><line x1=".5" y1="3.5" x2="8.5" y2="3.5" stroke="#8cc63f"/></svg>02/07/2016</span><span><svg width="11" height="9"><ellipse cx="5.5" cy="4" rx="5" ry="3.6" fill="#8cc63f"/></svg>21 commets</span><span><svg width="11" height="10"><path d="M1 4h2v6H1zM4 4l3-4c1 0 1.5.5 1 2.5h2.5c.6 0 1 .6.8 1.2L10 9.5H4z" fill="#8cc63f"/></svg>Like Us</span><span><svg width="10" height="10"><circle cx="8" cy="2" r="1.6" fill="#8cc63f"/><circle cx="2" cy="5" r="1.6" fill="#8cc63f"/><circle cx="8" cy="8" r="1.6" fill="#8cc63f"/><path d="M8 2L2 5l6 3" stroke="#8cc63f" fill="none"/></svg>Share</span></div>
    <p>Lorem ipsum dolor sit amet, consecit adipiscing elit, sed do eiusmod tempor incidimen labore n dolorme laboris ni ut aliquip ex ena lin consequat Duis aute lorem is irure dolor in reprehenderit magna aliqua. Ut enim ad is qnexercitation ullamco.</p>
    <span class="more"><svg width="27" height="27"><path d="M10 9l4 4.5-4 4.5M14 9l4 4.5-4 4.5" stroke="#fff" stroke-width="1.3" fill="none"/></svg></span>
  </article>

  <article class="post abs" style="top:1273px">
    <div class="thumb" role="img" aria-label="Happy couple embracing against a white background" style="background:linear-gradient(135deg,#f2ece8,#c89c82 45%,#6b4a3a 75%,#e9e9e9)"></div>
    <h3>Lorem ipsum dolor sit</h3>
    <div class="meta"><span><svg width="9" height="9"><rect x=".5" y="1.5" width="8" height="7" fill="none" stroke="#8cc63f"/><line x1=".5" y1="3.5" x2="8.5" y2="3.5" stroke="#8cc63f"/></svg>02/07/2016</span><span><svg width="11" height="9"><ellipse cx="5.5" cy="4" rx="5" ry="3.6" fill="#8cc63f"/></svg>21 commets</span><span><svg width="11" height="10"><path d="M1 4h2v6H1zM4 4l3-4c1 0 1.5.5 1 2.5h2.5c.6 0 1 .6.8 1.2L10 9.5H4z" fill="#8cc63f"/></svg>Like Us</span><span><svg width="10" height="10"><circle cx="8" cy="2" r="1.6" fill="#8cc63f"/><circle cx="2" cy="5" r="1.6" fill="#8cc63f"/><circle cx="8" cy="8" r="1.6" fill="#8cc63f"/><path d="M8 2L2 5l6 3" stroke="#8cc63f" fill="none"/></svg>Share</span></div>
    <p>Lorem ipsum dolor sit amet, consecit adipiscing elit, sed do eiusmod tempor incidimen labore n dolorme laboris ni ut aliquip ex ena lin consequat Duis aute lorem is irure dolor in reprehenderit magna aliqua. Ut enim ad is qnexercitation ullamco.</p>
    <span class="more"><svg width="27" height="27"><path d="M10 9l4 4.5-4 4.5M14 9l4 4.5-4 4.5" stroke="#fff" stroke-width="1.3" fill="none"/></svg></span>
  </article>

  <!-- sidebar -->
  <aside class="box abs" style="top:438px;height:89px">
    <div class="box-title"><svg width="16" height="16"><path d="M2 14a12 12 0 0 1 12-12M2 14a7 7 0 0 1 7-7" stroke="#8cc63f" stroke-width="2.2" fill="none"/><circle cx="3" cy="13" r="2" fill="#8cc63f"/></svg><span><em>Search</em> Blog</span></div>
    <div class="search-input">Search...<svg width="11" height="11"><circle cx="4.5" cy="4.5" r="3.5" fill="none" stroke="#bbb" stroke-width="1.2"/><line x1="7" y1="7" x2="10" y2="10" stroke="#bbb" stroke-width="1.2"/></svg></div>
  </aside>

  <aside class="box abs" style="top:557px;height:300px">
    <div class="tabs"><span><i></i>Friendly</span><span><i></i>Chirper</span><span><i></i>Snapgram</span></div>
    <ul class="feed">
      <li><div class="face" role="img" aria-label="Profile photo"></div><div><p>Lorem Ipsum is simply dummy text of the. printing and typesetting...</p><span class="like"><svg width="7" height="7"><path d="M0 3h1.5v4H0zM2 3l2-3c1 0 1 .5.8 2H7v1.5L6 7H2z" fill="#4a5e8c"/></svg>Like</span></div></li>
      <li><div class="face" role="img" aria-label="Profile photo"></div><div><p>Lorem Ipsum is simply dummy text of the. printing and typesetting...</p><span class="like"><svg width="7" height="7"><path d="M0 3h1.5v4H0zM2 3l2-3c1 0 1 .5.8 2H7v1.5L6 7H2z" fill="#4a5e8c"/></svg>Like</span></div></li>
      <li><div class="face" role="img" aria-label="Profile photo"></div><div><p>Lorem Ipsum is simply dummy text of the. printing and typesetting...</p><span class="like"><svg width="7" height="7"><path d="M0 3h1.5v4H0zM2 3l2-3c1 0 1 .5.8 2H7v1.5L6 7H2z" fill="#4a5e8c"/></svg>Like</span></div></li>
      <li><div class="face" role="img" aria-label="Profile photo"></div><div><p>Lorem Ipsum is simply dummy text of the. printing and typesetting...</p><span class="like"><svg width="7" height="7"><path d="M0 3h1.5v4H0zM2 3l2-3c1 0 1 .5.8 2H7v1.5L6 7H2z" fill="#4a5e8c"/></svg>Like</span></div></li>
    </ul>
  </aside>

  <aside class="box abs" style="top:886px;height:183px">
    <div class="box-title" style="height:36px"><svg width="12" height="16"><path d="M1 1h7l3 3v11H1z" fill="none" stroke="#8cc63f" stroke-width="1.4"/><line x1="6" y1="5" x2="6" y2="11" stroke="#8cc63f" stroke-width="1.4"/></svg><em>Archives</em></div>
    <ul class="archive">
      <li>June2016</li><li>July 2016</li><li>August 2016</li><li>September 2016</li><li>October 2016</li>
    </ul>
  </aside>

  <aside class="box abs" style="top:1098px;height:154px">
    <div class="box-title" style="height:36px"><svg width="20" height="16"><path d="M2 1h13a1.5 1.5 0 0 1 1.5 1.5v7A1.5 1.5 0 0 1 15 11H8l-4 4v-4H2A1.5 1.5 0 0 1 .5 9.5v-7A1.5 1.5 0 0 1 2 1z" fill="#8cc63f"/></svg><em>FAQ's</em><span class="view-all">View All</span></div>
    <ul class="faq">
      <li class="open"><svg width="11" height="8"><path d="M1 4l3 3 6-6" stroke="#8cc63f" stroke-width="1.5" fill="none"/></svg>Lorem ipsum dolor sit amet, consecit adipiscing elit, sed do ?</li>
      <li><span class="dot"></span>Lorem ipsum dolor sit amet, cons ecit adipiscing elit, sed do</li>
    </ul>
  </aside>

  <aside class="box abs" style="top:1281px;height:153px">
    <div class="box-title"><span><em>NewsLetter</em> SignUp</span></div>
    <div class="news">
      <p>Lorem ipsum dolor sit amet, cons ecit</p>
      <div class="field">Enter your email address</div>
      <span class="btn">DELIVERY</span>
    </div>
  </aside>

  <footer class="site-footer abs">Copyright © 2016 Tandem K. All rights reserved.</footer>
</div>
</body>
</html>
```